Design Website to Recruit next Generation of Steel Harbor's Order Vantage

Design a cool website that provides just enough information to be intriguing to teenagers who compete in combat sports. The format is to make this an invite-only team of high-school-aged competitors in combat sports (predominately Jiu Jitsu right now). Cinder Ravens can participate in similar assignments to earn consideration. We are modeled after the Order Vantage formed in Steel Harbor and would like to keep that look and feel. The document attached "OV - Ideas and Content for Website" shows our initial thoughts and here is more about us:

Goal - To promote the success of committed teenage Jiu Jitsu competitors who excel through focused preparation and deliberate practice.

Why - Prove the core principles of success.

How - Success is its own reward and always entails an element of the unknown/uncontrollable. We reward preparation. Setting clear goals (SMART), deliberate practice, building mental models (domain specific knowledge), restorative recovery, nutritional coaching, power of teaching others, sports science (strength & conditioning), expert guidance, personalized development plans, accountability, Quantified Self, gamification and competitive challenges. What - We will win at the highest of levels across the fight world by applying the general principles of success. These lessons will be carried with them to other areas of their lives.

Our primary goal with the website would be to share our company’s mission statement and promote the success of our sponsored athletes.

The only social media account we have currently is Pixtrelle's @ordervantageK7 (recently established). If you want more of an idea for what our online presence should feel like, then I would suggest watching these two scenes from Steel Harbor:

Recruiting: This scene shows the process for joining Order Vantage: https://vidrelo.net/Qk82LmTrA

Order Vantage Assignments: This shows how assignments are handed out for members to accomplish: https://vidrelo.net/Zp41XwNeB

Order Vantage Color Assignment: This is their first large assignment and where the green color comes from: https://vidrelo.net/Hd67VcJuC

It is also worth noting that "less is more" considering the first rule is, "you do not talk about..." That should carry over to our website and social media presence. We want to share just enough to be intriguing to inquiring minds and motivational for members, but no more.

I have uploaded a bunch of content, but just wanted to give you a broader idea. Feel free to design as you see fit...
Updates

Please stay tuned for the "burning smiley face" files. I have purchased a rendering of it so we have a proprietary vector image to use on our site. There will also be files for different versions of the Order Vantage//OV logos for various subcategories. Here is how they are to be applied: Circled = Primary (for main/landing page), Jiu Jitsu = Pyramid, Wrestling = Traditional, Muay Thai = Rolled, and Legacy OV = Original (coming soon).

Target Market(s)

Teenage competitors of combat sports, their parents, and sponsors of those athletes

Industry/Entity Type

Martial Arts & High School Sports

Coding

Coded - Design and coding required

Number of Pages Required

5+ page

Font styles to use
Sans Serif
Other font styles liked:
• See font in "Circled Logo"

Colors
59FF00
82FF00
B8FF75
E3FFCB
F4FFEA
EB3D1F
EC4F4E
F09395
F8D3D4
FCEDEE

Requirements
Must have
• Cool landing page with logo and brief summary of what we do. Page with 8 rules and explanation for earning an invitation. Plus, accomplishments page for memorializing the success of sponsored "Cinder Ravens"
Should not have
• Individual names

```html
<!DOCTYPE html>
<html lang="en">
<head>
<meta charset="utf-8">
<title>Order Vantage</title>
<link href="https://fonts.googleapis.com/css2?family=Exo+2:wght@700;800&family=Open+Sans:wght@400;600&display=swap" rel="stylesheet">
<style>
:root{
  --green:#7dc242;
  --green-deep:#43a047;
  --lime:#c0ca33;
  --ink:#222222;
  --text:#333333;
  --muted:#555555;
  --dark:#262626;
  --panel:#f4faee;
  --white:#ffffff;
}
*{box-sizing:border-box;margin:0;padding:0}
html,body{width:1200px;height:2642px;overflow:hidden;background:var(--white)}
body{position:relative;font-family:"Open Sans",sans-serif;color:var(--text)}
.display{font-family:"Exo 2",sans-serif;font-weight:800}
.abs{position:absolute}
.center{left:0;width:1200px;text-align:center}

/* hero */
.hero{position:absolute;top:0;left:0;width:1200px;height:514px}
.hero-photo{position:absolute;inset:0;background:linear-gradient(100deg,#6f6f6f 0%,#8c8c8c 40%,#a3a3a3 62%,#7a7a7a 100%)}
.hero-band{position:absolute;left:0;top:0;width:1200px;height:170px;background:linear-gradient(180deg,rgba(60,60,60,.55),rgba(60,60,60,.15))}
.brand{position:absolute;left:112px;top:12px;display:flex;align-items:center;gap:16px}
.brand-dot{width:72px;height:72px;border-radius:50%;background:#111;border:4px solid var(--green)}
.brand-name{font-family:"Exo 2",sans-serif;font-weight:800;font-size:30px;color:var(--white)}
.menu{position:absolute;left:1067px;top:41px;width:22px}
.menu span{display:block;height:3px;background:var(--white);margin-bottom:4px;border-radius:1px}
.hero-title{position:absolute;left:112px;top:182px;width:520px;font-size:39px;line-height:55px;color:rgba(255,255,255,.85)}

/* mission */
.kicker{top:578px;font-size:34px;color:var(--green)}
.subtitle{top:618px;font-size:34px;color:var(--ink)}
.rule{position:absolute;left:558px;width:84px;height:3px;background:var(--ink)}
.rule.light{background:var(--white)}
.lead{top:727px;font-size:19px;line-height:30px;color:var(--ink)}
.lead b{font-weight:600}
.trust{top:805px;font-size:29px;color:var(--ink)}
.trust em{font-style:normal;color:var(--green)}
.wheel{position:absolute;left:350px;top:879px}
.pillar{position:absolute;text-align:center;font-family:"Exo 2",sans-serif;font-weight:800}
.pillar h3{font-size:22px;margin-bottom:8px}
.pillar p{font-size:23px;line-height:26px;color:var(--muted)}

/* rules */
.rules{position:absolute;top:1535px;left:0;width:1200px;height:572px;background:var(--dark)}
.rules-photo{position:absolute;left:0;top:0;width:600px;height:572px;background:linear-gradient(90deg,#5a5a5a 0%,#444 55%,rgba(38,38,38,0) 100%)}
.rules h2{position:absolute;left:0;top:52px;width:1200px;text-align:center;font-size:36px;color:var(--green)}
.rule-list{position:absolute;left:507px;top:155px;list-style:none}
.rule-list li{display:flex;align-items:center;gap:14px;height:34.3px;font-size:18px;color:#eeeeee}
.rule-list svg{flex:none}
.rules blockquote{position:absolute;left:0;top:461px;width:1200px;text-align:center;font-size:22px;line-height:26px;color:#d6d6d6}

/* faq */
.faq-title{top:2148px;font-size:36px;color:var(--green)}
.faq{position:absolute;left:159px;width:882px}
.faq-head{height:66px;border-radius:33px;background:var(--dark);display:flex;align-items:center;padding:0 48px;color:var(--white);font-size:18px;position:relative;z-index:1}
.faq-head span.q{flex:1;margin-left:14px}
.faq-head .sign{font-size:26px;font-weight:400}
.faq-body{margin-top:-33px;padding:55px 52px 0;height:106px;background:var(--panel);border-radius:0 0 33px 33px;font-size:15px;color:var(--text)}
.cta{position:absolute;left:526px;top:2510px;width:149px;height:48px;background:var(--green);color:var(--white);font-weight:600;font-size:16px;display:flex;align-items:center;justify-content:center}
.footer{position:absolute;left:0;top:2585px;width:1200px;height:57px;background:var(--dark);color:var(--white);font-size:16px;display:flex;align-items:center;justify-content:center}
</style>
</head>
<body>

<header class="hero">
  <div class="hero-photo" role="img" aria-label="Black and white photo of two judo athletes mid-throw on a training mat"></div>
  <div class="hero-band"></div>
  <div class="brand"><div class="brand-dot"></div><span class="brand-name">Order Vantage</span></div>
  <div class="menu"><span></span><span></span><span></span></div>
  <h1 class="hero-title display">How much can you know about yourself if you've never been in a fights?</h1>
</header>

<section>
  <h2 class="abs center display kicker">Corvin Built Himself An Army</h2>
  <h2 class="abs center display subtitle">Why was Corvin Building an Army?</h2>
  <div class="rule" style="top:671px"></div>
  <p class="abs center lead">To introduce and apply the core principles of success to highschool aged <b>Jiu Jitsu</b> competitors.<br>We strive to work smarter not just harder so they can achieve their full potential success.</p>
  <h3 class="abs center display trust">IN CORVIN <em>WE TRUST</em></h3>

  <svg class="wheel" width="500" height="500" viewBox="0 0 500 500" aria-label="Wheel of training principles">
    <defs>
      <filter id="soft" x="-20%" y="-20%" width="140%" height="140%"><feDropShadow dx="0" dy="4" stdDeviation="10" flood-color="#000" flood-opacity=".12"/></filter>
    </defs>
    <circle cx="250" cy="250" r="246" fill="#fff" filter="url(#soft)"/>
    <g fill="none">
      <circle cx="250" cy="250" r="157" stroke="#c0ca33" stroke-width="96" stroke-dasharray="103 883" transform="rotate(-128 250 250)"/>
      <circle cx="250" cy="250" r="157" stroke="#43a047" stroke-width="96" stroke-dasharray="103 883" transform="rotate(-88 250 250)"/>
      <circle cx="250" cy="250" r="157" stroke="#43a047" stroke-width="96" stroke-dasharray="103 883" transform="rotate(-48 250 250)"/>
      <circle cx="250" cy="250" r="157" stroke="#43a047" stroke-width="96" stroke-dasharray="103 883" transform="rotate(-8 250 250)"/>
      <circle cx="250" cy="250" r="157" stroke="#7cb342" stroke-width="96" stroke-dasharray="103 883" transform="rotate(32 250 250)"/>
      <circle cx="250" cy="250" r="157" stroke="#7cb342" stroke-width="96" stroke-dasharray="103 883" transform="rotate(72 250 250)"/>
      <circle cx="250" cy="250" r="157" stroke="#7cb342" stroke-width="96" stroke-dasharray="103 883" transform="rotate(112 250 250)"/>
      <circle cx="250" cy="250" r="157" stroke="#c0ca33" stroke-width="96" stroke-dasharray="103 883" transform="rotate(152 250 250)"/>
      <circle cx="250" cy="250" r="157" stroke="#c0ca33" stroke-width="96" stroke-dasharray="103 883" transform="rotate(192 250 250)"/>

      <circle cx="250" cy="250" r="104" stroke="#9e9d24" stroke-width="12" stroke-dasharray="72 582" transform="rotate(-130 250 250)"/>
      <circle cx="250" cy="250" r="104" stroke="#2e7d32" stroke-width="12" stroke-dasharray="218 436" transform="rotate(-90 250 250)"/>
      <circle cx="250" cy="250" r="104" stroke="#558b2f" stroke-width="12" stroke-dasharray="218 436" transform="rotate(30 250 250)"/>
      <circle cx="250" cy="250" r="104" stroke="#9e9d24" stroke-width="12" stroke-dasharray="146 508" transform="rotate(150 250 250)"/>
    </g>
    <circle cx="250" cy="250" r="98" fill="#fff"/>
    <g fill="#fff" font-family="Open Sans, sans-serif" font-size="15.5" text-anchor="middle">
      <text x="205" y="90">Personalize<tspan x="205" dy="21">goals for</tspan><tspan x="205" dy="21">each</tspan></text>
      <text x="312" y="104">Privates<tspan x="312" dy="21">&amp; challenges</tspan></text>
      <text x="386" y="175">Drills &amp;<tspan x="386" dy="21">Spariy</tspan></text>
      <text x="401" y="277">Videos<tspan x="401" dy="21">past fights</tspan></text>
      <text x="343" y="365">Strong &amp;<tspan x="343" dy="21">Condition</tspan></text>
      <text x="248" y="408">Nutrition</text>
      <text x="145" y="366">Recovery</text>
      <text x="93" y="277">Fun trips<tspan x="93" dy="21">outing</tspan></text>
      <text x="117" y="175">Help young<tspan x="117" dy="21">competitions</tspan></text>
    </g>
  </svg>

  <div class="pillar" style="left:108px;top:1010px;width:240px">
    <h3 style="color:var(--lime)">SPIRIT</h3>
    <p>Without pain<br>without sacrifice we<br>would have nothing</p>
  </div>
  <div class="pillar" style="left:853px;top:1010px;width:240px">
    <h3 style="color:var(--green-deep)">TECHINCAL/MIND</h3>
    <p>Success is its own<br>rewardso we<br>celebrate<br>preparation</p>
  </div>
  <div class="pillar" style="left:250px;top:1407px;width:700px">
    <h3 style="color:var(--green)">BODY</h3>
    <p>When the fight was over nothing was solved but nothing<br>mattered we all felt saved</p>
  </div>
</section>

<section class="rules">
  <div class="rules-photo" role="img" aria-label="Black and white photo of two grapplers training on a mat"></div>
  <h2 class="display">I don't want to die without any scars</h2>
  <div class="rule light" style="top:111px"></div>
  <ul class="rule-list">
    <li><svg width="16" height="16" viewBox="0 0 16 16"><circle cx="8" cy="8" r="6.5" fill="none" stroke="#7dc242" stroke-width="2"/><path d="M5 8.2l2 2 4-4" fill="none" stroke="#7dc242" stroke-width="2"/></svg>Do not talk about OV</li>
    <li><svg width="16" height="16" viewBox="0 0 16 16"><circle cx="8" cy="8" r="6.5" fill="none" stroke="#7dc242" stroke-width="2"/><path d="M5 8.2l2 2 4-4" fill="none" stroke="#7dc242" stroke-width="2"/></svg>Do not talk about OV</li>
    <li><svg width="16" height="16" viewBox="0 0 16 16"><circle cx="8" cy="8" r="6.5" fill="none" stroke="#7dc242" stroke-width="2"/><path d="M5 8.2l2 2 4-4" fill="none" stroke="#7dc242" stroke-width="2"/></svg>You protect the reputation of past present and future OV athletes</li>
    <li><svg width="16" height="16" viewBox="0 0 16 16"><circle cx="8" cy="8" r="6.5" fill="none" stroke="#7dc242" stroke-width="2"/><path d="M5 8.2l2 2 4-4" fill="none" stroke="#7dc242" stroke-width="2"/></svg>You do not contest close matches or complain</li>
    <li><svg width="16" height="16" viewBox="0 0 16 16"><circle cx="8" cy="8" r="6.5" fill="none" stroke="#7dc242" stroke-width="2"/><path d="M5 8.2l2 2 4-4" fill="none" stroke="#7dc242" stroke-width="2"/></svg>You will serve as a bridge between kid &amp; adult B55 competition</li>
    <li><svg width="16" height="16" viewBox="0 0 16 16"><circle cx="8" cy="8" r="6.5" fill="none" stroke="#7dc242" stroke-width="2"/><path d="M5 8.2l2 2 4-4" fill="none" stroke="#7dc242" stroke-width="2"/></svg>You will attend teammate matches and help them whenever possible</li>
    <li><svg width="16" height="16" viewBox="0 0 16 16"><circle cx="8" cy="8" r="6.5" fill="none" stroke="#7dc242" stroke-width="2"/><path d="M5 8.2l2 2 4-4" fill="none" stroke="#7dc242" stroke-width="2"/></svg>You will always treat competitors with respect</li>
    <li><svg width="16" height="16" viewBox="0 0 16 16"><circle cx="8" cy="8" r="6.5" fill="none" stroke="#7dc242" stroke-width="2"/><path d="M5 8.2l2 2 4-4" fill="none" stroke="#7dc242" stroke-width="2"/></svg>If you are in then you have to fight</li>
  </ul>
  <blockquote class="display">I'm breaking my attachment to physical power and possessions, because only through<br>destroying myself can I discover the greater power of my spirit.</blockquote>
</section>

<section>
  <h2 class="abs center display faq-title">Common Questions</h2>
  <div class="rule" style="top:2209px"></div>
  <div class="faq" style="top:2250px">
    <div class="faq-head">
      <svg width="15" height="15" viewBox="0 0 16 16"><circle cx="8" cy="8" r="7" fill="#7dc242"/><path d="M4.5 8h6M8 5l3 3-3 3" fill="none" stroke="#262626" stroke-width="2"/></svg>
      <span class="q">Why the "K7"?</span><span class="sign">+</span>
    </div>
  </div>
  <div class="faq" style="top:2336px">
    <div class="faq-head">
      <svg width="15" height="15" viewBox="0 0 16 16"><circle cx="8" cy="8" r="7" fill="#7dc242"/><path d="M4.5 8h6M8 5l3 3-3 3" fill="none" stroke="#262626" stroke-width="2"/></svg>
      <span class="q">How does someone get invited?</span><span class="sign">-</span>
    </div>
    <div class="faq-body">We are accepting indications of interest form competitors born in 2007 &amp; 2008</div>
  </div>
  <a class="cta">Learn More</a>
</section>

<footer class="footer">2023 Order Vantage. All Rights Reserved.</footer>

</body>
</html>
```